Business Card Design

WE are looking for a premium quality Business Cards for a Law Firm . Copies of our current business card is attached.

Contact Information for Business Card

xyz

```html
<!DOCTYPE html>
<html lang="en">
<head>
<meta charset="utf-8">
<title>Ashcombe Lawyers – Business Card</title>
<link rel="stylesheet" href="https://fonts.googleapis.com/css2?family=Libre+Baskerville:wght@400;700&display=swap">
<style>
  :root {
    --backdrop: #2a2d33;
    --card-white: #f4f4f4;
    --ink: #141414;
    --firm-green: #0c2a1c;
    --firm-green-deep: #071a11;
    --gold: #c2a04f;
    --gold-pale: #ece5d6;
    --grey-soft: #c9cac8;
    --white: #ffffff;
  }
  * { box-sizing: border-box; margin: 0; padding: 0; }
  html, body {
    width: 1200px; height: 780px; overflow: hidden;
    background: var(--backdrop);
    font-family: "Libre Baskerville", Georgia, serif;
  }
  .canvas { position: relative; width: 1200px; height: 780px; }

  .card {
    position: absolute; top: 235px; width: 540px; height: 310px;
    overflow: hidden; box-shadow: 0 14px 30px rgba(0,0,0,.45);
  }
  .card-front { left: 40px; background: var(--card-white); color: var(--ink); }
  .card-back { left: 620px; background: var(--firm-green); }

  /* firm name block */
  .firm-mark { position: absolute; display: flex; flex-direction: column; align-items: center; }
  .firm-mark .ring { border-radius: 50%; }
  .firm-mark .firm-name {
    font-weight: 700; text-align: center; line-height: 1.1;
  }
  .firm-mark .firm-name small { display: block; letter-spacing: .35em; }

  .card-front .firm-mark { left: 34px; top: 22px; }
  .card-front .ring { width: 40px; height: 40px; border: 3px solid var(--gold); margin-bottom: 6px; }
  .card-front .firm-name { color: var(--firm-green); font-size: 19px; }
  .card-front .firm-name small { font-size: 8px; margin-top: 2px; }

  .address {
    position: absolute; left: 34px; top: 118px;
    font-size: 11.5px; font-weight: 700; line-height: 1.45;
  }
  .contacts {
    position: absolute; left: 34px; top: 176px; list-style: none;
    font-size: 11.5px; font-weight: 700; line-height: 1.5;
  }
  .contacts li { display: flex; align-items: center; gap: 8px; }
  .contacts svg { width: 11px; height: 11px; flex: none; }

  .monogram-field {
    position: absolute; left: 250px; top: 70px; width: 300px; height: 300px;
    border-radius: 50%;
    background: radial-gradient(circle, var(--card-white) 48%, var(--gold-pale) 50%, var(--gold-pale) 56%, rgba(236,229,214,.3) 60%, transparent 68%);
  }
  .person {
    position: absolute; right: 40px; top: 132px; text-align: right;
  }
  .person .name {
    color: var(--gold); font-size: 27px; font-weight: 700; letter-spacing: .02em;
    text-transform: uppercase; line-height: 1.1;
  }
  .person .role, .person .credentials { font-size: 12px; font-weight: 700; line-height: 1.55; }
  .gold-band {
    position: absolute; right: 78px; bottom: 0; width: 44px; height: 78px; background: var(--gold);
  }

  .pattern-field {
    position: absolute; inset: 0;
    background: linear-gradient(115deg, var(--firm-green-deep) 0%, var(--firm-green) 55%, #24473a 100%);
  }
  .card-back .firm-mark { right: 34px; bottom: 26px; }
  .card-back .ring { width: 26px; height: 26px; border: 2px solid var(--white); margin-bottom: 4px; }
  .card-back .firm-name { color: var(--white); font-size: 12px; }
  .card-back .firm-name small { font-size: 6px; margin-top: 1px; }
</style>
</head>
<body>
<main class="canvas">

  <section class="card card-front" aria-label="Business card front">
    <div class="firm-mark">
      <span class="ring"></span>
      <p class="firm-name">ASHCOMBE<small>LAWYERS</small></p>
    </div>

    <address class="address">
      Level 2, Harrow Chambers,<br>
      48 Harrow Street,<br>
      Northgate, QLD 4013
    </address>

    <ul class="contacts">
      <li>
        <svg viewBox="0 0 12 12" aria-hidden="true"><path d="M3 1l2 2.5-1.2 1.3a7 7 0 0 0 3.4 3.4L8.5 7 11 9l-1 2C5 11 1 7 1 2z" fill="none" stroke="#c2a04f" stroke-width="1.2"/></svg>
        +61 7 3555 0142
      </li>
      <li>
        <svg viewBox="0 0 12 12" aria-hidden="true"><rect x="3" y="1" width="6" height="10" rx="1" fill="none" stroke="#c2a04f" stroke-width="1.2"/></svg>
        +61 0400 555 218
      </li>
      <li>
        <svg viewBox="0 0 12 12" aria-hidden="true"><circle cx="6" cy="6" r="5" fill="none" stroke="#c2a04f" stroke-width="1.2"/><path d="M1 6h10M6 1c-2.5 3-2.5 7 0 10M6 1c2.5 3 2.5 7 0 10" fill="none" stroke="#c2a04f" stroke-width="1"/></svg>
        www.ashcombelawyers.com.au
      </li>
      <li>
        <svg viewBox="0 0 12 12" aria-hidden="true"><rect x="1" y="2.5" width="10" height="7" fill="none" stroke="#c2a04f" stroke-width="1.2"/><path d="M1 2.5l5 4 5-4" fill="none" stroke="#c2a04f" stroke-width="1.2"/></svg>
        daniel@ashcombelawyers.com.au
      </li>
    </ul>

    <div class="monogram-field" role="img" aria-label="Faint large firm monogram decoration"></div>

    <div class="person">
      <p class="name">Daniel Mercer</p>
      <p class="role">Director and Principal Solicitor</p>
      <p class="credentials">MBA, Juris Doctor</p>
    </div>

    <span class="gold-band"></span>
  </section>

  <section class="card card-back" aria-label="Business card back">
    <div class="pattern-field" role="img" aria-label="Repeating firm monogram pattern fading across dark green"></div>
    <div class="firm-mark">
      <span class="ring"></span>
      <p class="firm-name">ASHCOMBE<small>LAWYERS</small></p>
    </div>
  </section>

</main>
</body>
</html>
```